Business Card Design

Business Card for professional consulting firm working with large financial institutions.

Target Market(s)

Executive buyers

Industry/Entity Type

Banking

Contact Information for Business Card

Mild creativity wanted. Not boring, but do elaborate artwork.

Font styles to use
Serif
Sans Serif

Colors

Designer to choose colors to be used in the design.

Requirements
Must have
• Standard business card features - company name, individual name, telephone, website, email, locations.
Nice to have
• Two colors
Should not have
• too many colors, fancy printing, cartoons.

```html
<!DOCTYPE html>
<html lang="en">
<head>
<meta charset="UTF-8">
<title>Northvale – Business Card</title>
<link rel="stylesheet" href="https://fonts.googleapis.com/css2?family=Lato:wght@400;700&display=swap">
<style>
  :root {
    --navy: #002d80;
    --silver: #c9cacd;
    --disc: #f3f3f5;
    --white: #ffffff;
    --backdrop: #e6e7ea;
  }
  html, body {
    margin: 0;
    padding: 0;
    width: 1200px;
    height: 900px;
    overflow: hidden;
    background: var(--backdrop);
    font-family: "Lato", Arial, sans-serif;
  }
  .business-card {
    position: absolute;
    left: 100px;
    top: 164px;
    width: 1000px;
    height: 572px;
    border-radius: 16px;
    overflow: hidden;
    background: var(--silver);
    box-shadow: 0 10px 30px rgba(0, 0, 0, 0.12);
  }
  .navy-panel {
    position: absolute;
    left: 0;
    top: 0;
    width: 677px;
    height: 100%;
    background: var(--navy);
  }
  .brand-disc {
    position: absolute;
    left: 415px;
    top: 16px;
    width: 540px;
    height: 540px;
    border-radius: 50%;
    background: radial-gradient(circle at 50% 45%, var(--white) 0%, var(--disc) 70%, #e9e9ec 100%);
    display: flex;
    align-items: center;
    justify-content: center;
  }
  .brand-name {
    font-family: "Lato", Arial, sans-serif;
    font-weight: 400;
    font-size: 58px;
    color: var(--navy);
    letter-spacing: 0.5px;
  }
  .identity {
    position: absolute;
    left: 42px;
    top: 88px;
    color: var(--white);
  }
  .person-name {
    margin: 0;
    font-size: 36px;
    font-weight: 700;
    letter-spacing: 0.5px;
    line-height: 1.1;
  }
  .person-role {
    margin: 4px 0 0;
    font-size: 27px;
    font-weight: 400;
  }
  .address {
    position: absolute;
    left: 44px;
    top: 264px;
    margin: 0;
    font-style: normal;
    font-size: 28px;
    line-height: 37px;
    color: var(--white);
  }
  .contact-list {
    position: absolute;
    left: 40px;
    top: 414px;
    margin: 0;
    padding: 0;
    list-style: none;
    color: var(--white);
    font-size: 28px;
    line-height: 37px;
  }
  .contact-list li {
    display: flex;
    align-items: center;
    gap: 8px;
  }
  .contact-icon {
    width: 20px;
    height: 20px;
    fill: var(--white);
    flex: none;
  }
</style>
</head>
<body>
  <main class="business-card">
    <div class="navy-panel"></div>
    <div class="brand-disc">
      <span class="brand-name">Northvale</span>
    </div>

    <header class="identity">
      <h1 class="person-name">DANIEL HARROW</h1>
      <p class="person-role">Managing Director</p>
    </header>

    <address class="address">
      12345, Address<br>
      Goes Here<br>
      Country Name, 123456
    </address>

    <ul class="contact-list">
      <li>
        <svg class="contact-icon" viewBox="0 0 20 20" aria-hidden="true">
          <path d="M2 7c0-2 3-4 8-4s8 2 8 4v1.5h-4V7c-1-.6-2.4-.9-4-.9S7 6.4 6 7v1.5H2z"/>
          <path d="M5 10h10l2 7H3z"/>
        </svg>
        <span>044-123 456 789</span>
      </li>
      <li>
        <svg class="contact-icon" viewBox="0 0 20 20" aria-hidden="true">
          <path d="M2 4h16v12H2z M3.5 5.5 10 10.5 16.5 5.5" fill-rule="evenodd"/>
          <path d="M3 5l7 5.5L17 5" fill="none" stroke="#002d80" stroke-width="1.4"/>
        </svg>
        <span>hello@northvale-mail.com</span>
      </li>
      <li>
        <svg class="contact-icon" viewBox="0 0 20 20" aria-hidden="true">
          <circle cx="10" cy="10" r="8.5"/>
          <path d="M6 5.5c2 .5 3 1.5 2.5 3S6 10 6.5 12s2 2 2 4M12 3.5c-1 1.5 0 3 1.5 3.5s2.5 2 1.5 4-2.5 1.5-3 3.5" fill="none" stroke="#002d80" stroke-width="1.3"/>
        </svg>
        <span>www.northvale-site.com</span>
      </li>
    </ul>
  </main>
</body>
</html>
```